Give Gold Kite an Online Presence!

Gold Kite Property Maintenance is an Australian Owned property maintenance company who needs a stand out online presence.

GK maintains many buildings and sites and wants to appeal to a corporate professional market with their brand new website. GK is essentially a handyman service offering all maintenance services to home owners, office managers, real estate agents and strata managers.

The Website:
We need a corporate website that appeals to our broader customer base (property owners, property managers, office managers) the copy is being written by a professional so use filler text for now.

Things that we want:
Home page that sets us apart and appeals to the corporate and residential market. The home page needs to not focus on either the residential or commercial market. The home page should focus on our logo and branding. We have a logo already and it is attached to the brief, please use it and try to consider the colour pallette that goes with it. Whilst we want the site to appear strong and manly it is important to remember that 95% of our customers are female so we need the site to be appealing to women. Women need to believe that we are strong, dependable and trustworthy.
We'd like a quote page and potentially also the ability to get a quote from the home page (please don't put it in if it ruins the overall feel of the home page)
An "about us" page
A contact us page
A blog that's built in (we don't want to link to an external blog)
(overall we'd expect to have 6 or 7 pages total)

The site will also need coding - we expect this to be done in a separate project but need you to consider a few things about the coding side of things.

It needs to be iPhone and iPad compatible.

We'd like you to suggest the best CMS that you would use or if you would suggest not using a CMS please let us know with your submissions.

Target Market(s)

Property owners, office managers and property managers who need maintenance on buildings (So all of them)

Industry/Entity Type

Property Maintenance

Requirements
Must have
• Our Logo
Home page
About Us
Residential
Commercial
Real Estate/Strata
Contact Us/Quote
Blog
Nice to have
• Quote form included in home page
Movement on the home page at least
Should not have
• other logos, too much colour
NO FLASH

```html
<!DOCTYPE html>
<html lang="en">
<head>
<meta charset="utf-8">
<title>Gold Kite Property Maintenance</title>
<link rel="stylesheet" href="https://fonts.googleapis.com/css2?family=Ubuntu:wght@500;700&family=Open+Sans:wght@400;600&family=Montserrat:wght@300;400;700&family=Arimo:ital,wght@0,400;0,700;1,700&display=swap">
<style>
:root{
  --orange:#f68b1f;
  --orange-dark:#d9730f;
  --black:#0b0b0b;
  --nav:#151515;
  --paper:#f7f7f7;
  --ink:#222;
  --body:#555;
  --white:#fff;
}
*{margin:0;padding:0;box-sizing:border-box}
html,body{width:1200px;height:1156px;overflow:hidden}
body{position:relative;background:var(--paper);font-family:"Open Sans",sans-serif;color:var(--ink)}
.abs{position:absolute}

/* header */
.site-header{position:absolute;left:0;top:0;width:1200px;height:84px;background:var(--orange)}
.brand{position:absolute;left:176px;top:20px;color:var(--white);font-family:"Ubuntu",sans-serif;font-weight:700;line-height:1}
.brand-name{font-size:29px;letter-spacing:-.3px}
.brand-sub{font-size:15px;margin-top:2px;letter-spacing:.2px}
.contact-box{position:absolute;left:556px;top:10px;width:468px;height:64px;border:1px solid rgba(255,255,255,.55);border-radius:8px;background:rgba(255,255,255,.06)}
.contact-divider{position:absolute;left:210px;top:6px;width:1px;height:52px;background:rgba(255,255,255,.35)}
.give-line{position:absolute;left:86px;top:13px;font-family:"Ubuntu",sans-serif;font-weight:500;color:var(--white);font-size:15px}
.send-btn{position:absolute;left:82px;top:32px;width:114px;height:23px;border-radius:6px;background:var(--black);color:var(--white);font-family:"Arimo",sans-serif;font-weight:700;font-size:14px;text-align:center;line-height:23px}
.say-hello{position:absolute;left:289px;top:18px;font-family:"Ubuntu",sans-serif;font-weight:500;color:var(--white);font-size:15px}
.phone-number{position:absolute;left:288px;top:32px;font-family:"Arimo",sans-serif;font-weight:700;color:var(--white);font-size:24px;letter-spacing:.5px}

/* nav */
.main-nav{position:absolute;left:0;top:84px;width:1200px;height:54px;background:linear-gradient(#111,#2a2a2a 70%,#1c1c1c)}
.main-nav a{position:absolute;top:18px;color:var(--white);text-decoration:none;font-family:"Arimo",sans-serif;font-size:15px;letter-spacing:.2px}
.main-nav .active-tab{position:absolute;left:173px;top:0;width:68px;height:54px;background:linear-gradient(var(--orange),#e07a14);border-bottom:3px solid #b8600c}
.main-nav .active-tab::after{content:"";position:absolute;left:30px;bottom:-8px;border:5px solid transparent;border-top-color:#b8600c}

/* hero */
.hero{position:absolute;left:0;top:138px;width:1200px;height:356px}
.hero-band{position:absolute;left:0;top:493px;width:1200px;height:42px;background:var(--orange)}
.hero-band::before{content:"";position:absolute;left:200px;top:-4px;width:800px;height:22px;border-radius:50%;background:radial-gradient(ellipse at center,rgba(0,0,0,.65),rgba(0,0,0,0) 70%)}

/* services */
.service{position:absolute;top:580px;width:250px}
.service h2{font-family:"Montserrat",sans-serif;font-weight:700;color:var(--orange);font-size:17px;letter-spacing:1.3px;margin-bottom:4px}
.service p{font-size:13px;line-height:18px;color:var(--body);letter-spacing:.2px}
.shadow-bar{position:absolute;top:736px;width:240px;height:12px;border-radius:50%;background:radial-gradient(ellipse at center,rgba(0,0,0,.7),rgba(0,0,0,0) 72%)}

/* clients */
.clients-title{position:absolute;left:190px;top:810px;width:123px;text-align:right;font-family:"Montserrat",sans-serif;font-weight:400;font-size:31px;line-height:31px;color:var(--black)}
.client{position:absolute;top:803px;width:162px;height:81px;display:flex;align-items:center;justify-content:center;font-family:"Montserrat",sans-serif;font-weight:700;font-size:22px}
.client-a{left:346px;background:linear-gradient(135deg,#5fc4ee,#2aa2da);color:var(--white)}
.client-b{left:520px;width:160px;background:#0a0a0a;border:2px solid #e5a21a;color:#e5a21a}
.client-c{left:694px;background:linear-gradient(#fff,#e9e9e9);color:#999}
.client-d{left:866px;background:linear-gradient(#f4c21a 0 28%,#3a86b5 28%,#6cc06a);color:var(--white)}

/* footer */
.info-panel{position:absolute;left:173px;top:944px;width:855px;height:135px;background:var(--orange);font-family:"Arimo",sans-serif;color:#2a1a08}
.info-shadow{position:absolute;left:210px;top:1078px;width:780px;height:16px;border-radius:50%;background:radial-gradient(ellipse at center,rgba(0,0,0,.6),rgba(0,0,0,0) 72%)}
.testimonial{position:absolute;left:17px;top:16px}
.testimonial-label{font-weight:700;font-size:14px}
.testimonial-quote{font-style:italic;font-weight:700;font-size:22px;line-height:26px;margin-top:3px}
.testimonial-author{font-size:16px;margin-top:1px}
.dots{position:absolute;left:17px;top:110px;display:flex;gap:3px}
.dots span{width:10px;height:10px;border-radius:50%;background:#1a1a1a}
.dots span.current{background:var(--white)}
.office{position:absolute;left:293px;top:14px}
.panel-title{font-size:18px;font-weight:700;margin-bottom:3px}
.office p{font-size:12.5px;line-height:15px}
.quote-form{position:absolute;left:584px;top:14px}
.email-field{margin-top:6px;width:237px;height:31px;background:var(--white);border:3px solid var(--black);font-size:13px;color:#333;padding:5px 10px}
.submit-btn{margin-top:7px;width:103px;height:32px;background:var(--black);color:var(--white);font-weight:700;font-size:14px;display:flex;align-items:center;padding-left:16px;gap:10px;letter-spacing:.5px}
.copyright{position:absolute;left:0;width:1170px;top:1103px;text-align:center;font-family:"Arimo",sans-serif;font-weight:700;font-size:11px;color:#555}
.accent-line{position:absolute;left:178px;top:1118px;width:35px;height:4px;background:#fbe9a8}
</style>
</head>
<body>

<header class="site-header">
  <div class="brand">
    <div class="brand-name">GOLD KITE</div>
    <div class="brand-sub">PROPERTY MAINTENANCE</div>
  </div>
  <div class="contact-box">
    <svg class="abs" style="left:15px;top:12px" width="58" height="40" viewBox="0 0 58 40" aria-hidden="true">
      <rect x="1" y="1" width="56" height="38" rx="2" fill="#f4f4f4" stroke="#c9c9c9"/>
      <path d="M2 2 L29 24 L56 2" fill="none" stroke="#bdbdbd" stroke-width="2"/>
      <path d="M2 38 L22 19 M56 38 L36 19" stroke="#d0d0d0" stroke-width="1.5"/>
    </svg>
    <div class="give-line">Give a line</div>
    <div class="send-btn">Send Message</div>
    <div class="contact-divider"></div>
    <svg class="abs" style="left:222px;top:10px" width="60" height="44" viewBox="0 0 60 44" aria-hidden="true">
      <path d="M4 12 Q30 -2 56 12 L52 18 L42 16 L42 11 Q30 7 18 11 L18 16 L8 18 Z" fill="#1a1a1a"/>
      <path d="M14 20 L46 20 L54 42 L6 42 Z" fill="#1a1a1a"/>
      <circle cx="30" cy="30" r="9" fill="#e8a23a"/>
      <circle cx="30" cy="30" r="4" fill="#1a1a1a"/>
    </svg>
    <div class="say-hello">Say Hello</div>
    <div class="phone-number">0400 555 271</div>
  </div>
</header>

<nav class="main-nav">
  <div class="active-tab"></div>
  <a style="left:187px">HOME</a>
  <a style="left:258px">ABOUT US</a>
  <a style="left:361px">RESIDENTIAL</a>
  <a style="left:485px">COMMERCIAL</a>
  <a style="left:610px">REAL ESTATE/STRATA</a>
  <a style="left:795px">CONTACT US/QUOTE</a>
  <a style="left:971px">BLOG</a>
</nav>

<svg class="hero" viewBox="0 155 1349 400" preserveAspectRatio="none">
  <defs>
    <radialGradient id="heroGlow" cx="50%" cy="45%" r="45%">
      <stop offset="0" stop-color="#5a5a5a"/>
      <stop offset=".55" stop-color="#262626"/>
      <stop offset="1" stop-color="#000"/>
    </radialGradient>
    <linearGradient id="teamFill" x1="0" y1="0" x2="0" y2="1">
      <stop offset="0" stop-color="#1a1a1a"/>
      <stop offset=".7" stop-color="#0d0d0d"/>
      <stop offset="1" stop-color="#c86f12"/>
    </linearGradient>
  </defs>
  <rect x="0" y="155" width="1349" height="400" fill="url(#heroGlow)"/>
  <rect x="0" y="155" width="1349" height="30" fill="#000" opacity=".5"/>
  <rect x="540" y="200" width="270" height="245" rx="20" fill="url(#teamFill)" role="img" aria-label="Three maintenance workers in silhouette standing above a city skyline"/>
  <rect x="514" y="438" width="320" height="67" rx="12" fill="#f68b1f"/>
  <text x="674" y="468" text-anchor="middle" fill="#fff" font-family="Ubuntu, sans-serif" font-weight="700" font-size="30">GOLD KITE</text>
  <text x="674" y="493" text-anchor="middle" fill="#fff" font-family="Ubuntu, sans-serif" font-weight="700" font-size="21">PROPERTY MAINTENANCE</text>

  <g font-family="Arimo, sans-serif" font-weight="700" font-size="11.5" fill="#fff">
    <text x="316" y="230">All commercial and</text>
    <text x="316" y="245">residential handyman work</text>
    <text x="305" y="303">Strata management work</text>
    <text x="306" y="362">Scheduled maintenance</text>
    <text x="245" y="415">Pictures and whiteboards hung</text>
    <text x="377" y="465">Lighting</text>
    <text x="846" y="199">Carpentry</text>
    <text x="866" y="239">Doors and locks</text>
    <text x="872" y="283">Windows and screens</text>
    <text x="892" y="323">Furniture assembly</text>
    <text x="892" y="366">Office moves</text>
    <text x="903" y="408">Painting</text>
    <text x="903" y="453">All repairs</text>
  </g>
  <g fill="none" stroke="#f68b1f" stroke-width="2.5">
    <path d="M316 251 H487 L508 271"/>
    <path d="M305 311 H465 L488 331"/>
    <path d="M306 370 H463 L485 390"/>
    <path d="M245 423 H441 L463 443"/>
    <path d="M377 472 H441 L462 492"/>
    <path d="M911 206 H846 L826 227"/>
    <path d="M973 246 H866 L846 267"/>
    <path d="M1009 290 H872 L850 311"/>
    <path d="M1009 330 H892 L870 351"/>
    <path d="M979 374 H892 L872 394"/>
    <path d="M962 416 H903 L882 436"/>
    <path d="M968 461 H903 L882 481"/>
  </g>
  <g fill="#f68b1f" stroke="#7a4408" stroke-width="3" stroke-opacity=".8">
    <circle cx="508" cy="271" r="5"/><circle cx="488" cy="331" r="5"/><circle cx="485" cy="390" r="5"/>
    <circle cx="463" cy="443" r="5"/><circle cx="462" cy="492" r="5"/>
    <circle cx="826" cy="227" r="5"/><circle cx="846" cy="267" r="5"/><circle cx="850" cy="311" r="5"/>
    <circle cx="870" cy="351" r="5"/><circle cx="872" cy="394" r="5"/><circle cx="882" cy="436" r="5"/><circle cx="882" cy="481" r="5"/>
  </g>
</svg>
<div class="hero-band"></div>

<section class="service" style="left:189px">
  <h2>RESIDENTIAL</h2>
  <p>By nerds, for nerds.<br>Built at Birdhouse by @kel and @rob,<br>Scaffold utilizes TINY CSS, is com-<br>piled via Forge, and is managed<br>through CodeBarn to help nerds do<br>awesome stuff on the web.</p>
</section>
<div class="shadow-bar" style="left:182px"></div>

<section class="service" style="left:491px">
  <h2>COMMERCIAL</h2>
  <p>By nerds, for nerds.<br>Built at Birdhouse by @kel and @rob,<br>Scaffold utilizes TINY CSS, is com-<br>piled via Forge, and is managed<br>through CodeBarn to help nerds do<br>awesome stuff on the web.</p>
</section>
<div class="shadow-bar" style="left:484px"></div>

<section class="service" style="left:787px">
  <h2>REAL ESTATE/STRATA</h2>
  <p>By nerds, for nerds.<br>Built at Birdhouse by @kel and @rob,<br>Scaffold utilizes TINY CSS, is com-<br>piled via Forge, and is managed<br>through CodeBarn to help nerds do<br>awesome stuff on the web.</p>
</section>
<div class="shadow-bar" style="left:780px"></div>

<div class="clients-title">Our Clients</div>
<div class="client client-a">Arcline</div>
<div class="client client-b">Forgeworks</div>
<div class="client client-c">Northgrid</div>
<div class="client client-d">Vantis</div>

<div class="info-shadow"></div>
<footer class="info-panel">
  <div class="testimonial">
    <div class="testimonial-label">What They Said:</div>
    <div class="testimonial-quote">“Good Services,<br>Reasonable Price.”</div>
    <div class="testimonial-author">- Someone</div>
  </div>
  <div class="dots"><span></span><span></span><span class="current"></span></div>

  <div class="office">
    <div class="panel-title">Head Office</div>
    <p>Address 14 Harbour Lane<br>Carrington NSW 2294<br>Phone 02 4900 1827<br>Email hello@goldkitepm.com.au<br>Web www.goldkitepm.com.au</p>
  </div>

  <div class="quote-form">
    <div class="panel-title">Get a Quote Form</div>
    <div class="email-field">Your Email Address</div>
    <div class="submit-btn">SUBMIT
      <svg width="14" height="22" viewBox="0 0 14 22" aria-hidden="true"><path d="M3 2 L11 11 L3 20" fill="none" stroke="#fff" stroke-width="3"/></svg>
    </div>
  </div>
</footer>

<div class="copyright">Copyright 2011 © GK Property Maintenance - All Rights Reserved</div>
<div class="accent-line"></div>

</body>
</html>
```